Medical consulting firm needs polished website

I am a physician and working on setting up a smal consulting firm in New Hampshire, USA. It is called Bright Harbor Medical Services, LLC and the website will be BrightHarborMed.com. I was puttering around at making my own website, and it just didn't come together nicely so I've decided to leave it to the pros. The focus of the business is Advanced Care Planning, ie planning for your future medical needs. So it deals with some heavy stuff like planning for if you get sick, who should make decisions for you, end of life options etc. So it can't be too flippant or cutesy, but also can't be too dour and dark. I am hoping to convey that by thinking ahead and making some plans you can lift some of the worries off of yourself and your family - and that we can help make a scary sounding path more manageable. I want it to be made with wordpress and I have actually already bought a template ( Vitarun – A Modern Multidisciplinary Medical & Health Theme ). The website needs to have general information about our services, doc profile, appointment maker, blog/url link page, and ideally web commerce application ( the template has access to woocommerce). I've posted my business card and current brochure (still tweaking them, but you get the idea). I am also partnering with lumenfold.com and so have included their logo and would want connections/info about them. I have the logos etc in different formats as needed.

Target Market(s)

middle aged to older adults

Industry/Entity Type

Medical

Coding

Coded - Design and coding required

Font styles to use
Sans Serif

Requirements
Must have
• as above.
Nice to have
• Ease of reading/access for elderly viewers. woo commerce.

```html
<!DOCTYPE html>
<html lang="en">
<head>
<meta charset="utf-8">
<title>Bright Harbor Medical Services</title>
<link href="https://fonts.googleapis.com/css2?family=Open+Sans:wght@400;600;700&family=Raleway:wght@500;600;700&display=swap" rel="stylesheet">
<style>
:root{
  --blue:#1d5fa8;
  --blue-dark:#174f8e;
  --green:#3aa335;
  --green-light:#56b947;
  --text:#444;
  --muted:#777;
  --line:#e2e2e2;
  --grey:#ececec;
  --white:#fff;
}
*{box-sizing:border-box;margin:0;padding:0}
html,body{width:1200px;height:3315px;overflow:hidden}
body{font-family:"Open Sans",Arial,sans-serif;color:var(--text);background:var(--white);position:relative}
.abs{position:absolute}
h1,h2,h3,h4{font-family:"Raleway",Arial,sans-serif}
.btn{display:inline-block;background:var(--green);color:var(--white);font-size:17px;padding:15px 20px;text-decoration:none}

/* header */
.topbar{top:0;left:0;width:1200px;height:118px;border-top:4px solid var(--blue);border-bottom:1px solid var(--line)}
.brand{left:98px;top:26px;display:flex;align-items:center;gap:12px}
.brand-dot{width:62px;height:62px;border-radius:50%;background:var(--blue)}
.brand-name{font-family:"Raleway",sans-serif;font-size:34px;font-weight:600;color:var(--blue);line-height:1}
.info{top:34px;display:flex;gap:12px;font-size:14px}
.info svg{width:34px;height:34px}
.info b{display:block;color:#222;font-weight:600;margin-bottom:6px}
.info span{color:#999}
.socials{display:flex;gap:4px;margin-top:4px}
.socials i{width:22px;height:22px;border:1px solid #888;border-radius:50%;display:block}
.nav{top:118px;left:0;width:1200px;height:54px;border-bottom:1px solid var(--line)}
.nav ul{list-style:none;display:flex;gap:0;position:absolute;left:98px;top:18px;font-size:15px;color:#222}
.nav li{margin-right:62px}
.search{left:838px;top:6px;width:40px;height:40px;border:2px solid #333;display:flex;align-items:center;justify-content:center}
.book{left:905px;top:0;width:195px;height:54px;background:var(--green);color:var(--white);font-size:15px;display:flex;align-items:center;justify-content:center}

/* hero */
.hero{top:172px;left:0;width:1200px;height:520px;background:linear-gradient(90deg,#e7e4df 0%,#dcd4c8 45%,#c9b9a2 100%)}
.hero h1{position:absolute;left:98px;top:90px;font-size:38px;line-height:52px;color:var(--blue);font-weight:700}
.hero p{position:absolute;left:98px;top:200px;width:520px;font-size:15px;line-height:26px;color:#333}
.hero .btn{position:absolute;left:98px;top:290px}
.hero .arrows{position:absolute;left:98px;top:380px;display:flex;gap:8px}
.hero .arrows i{width:34px;height:34px;border:2px solid #333;border-radius:50%;display:block}
.hero-curve{top:600px;left:0}

/* welcome */
.badge{left:572px;top:706px;width:56px;height:56px;border-radius:50%;background:var(--blue);border:4px solid var(--white);box-shadow:0 0 0 3px var(--green)}
.section-title{width:1200px;text-align:center;font-size:32px;font-weight:600;color:var(--blue)}
.section-sub{left:200px;width:800px;text-align:center;font-size:13px;line-height:28px;color:var(--muted)}
.features{top:920px;left:80px;width:1040px;display:flex;justify-content:space-around}
.feature{width:300px;text-align:center;font-size:16px;line-height:28px;color:#444}
.feature svg{width:100px;height:100px;margin-bottom:30px}
.side-arrow{top:970px}

/* choose */
.choose{top:1145px;left:0;width:1200px;height:398px;background:var(--blue)}
.choose h2{position:absolute;left:98px;top:55px;font-size:28px;color:var(--white);font-weight:600}
.choose h4{position:absolute;left:98px;top:110px;width:440px;font-size:14px;line-height:26px;color:var(--white);font-weight:700}
.choose p{position:absolute;left:98px;top:170px;width:440px;font-size:13.5px;line-height:23px;color:#dce6f3}
.outline-btn{position:absolute;left:98px;top:285px;border:2px solid var(--white);color:var(--white);font-size:17px;padding:12px 18px}
.video{position:absolute;left:561px;top:57px;width:537px;height:281px;border:4px solid var(--white);background:linear-gradient(120deg,#7e5a43,#c49a7d 50%,#6d8cb5)}
.play{position:absolute;left:243px;top:115px;width:52px;height:52px;border-radius:50%;background:#111;border:3px solid var(--white)}
.play::after{content:"";position:absolute;left:19px;top:13px;border-left:18px solid var(--white);border-top:11px solid transparent;border-bottom:11px solid transparent}

/* people first */
.circles{top:1735px;left:0;width:1200px}
.circle-item{position:absolute;width:260px;text-align:center}
.ring{width:150px;height:150px;margin:0 auto;border-radius:50%;border:8px solid var(--green);box-shadow:0 0 0 4px var(--white),0 0 0 6px #b9e0b3}
.ring div{width:100%;height:100%;border-radius:50%}
.circle-item h3{margin-top:82px;font-size:18px;letter-spacing:.5px;color:var(--blue);font-weight:700}
.circle-item p{margin-top:14px;font-size:14px;line-height:22px;color:#555}

/* testimonials */
.reviews{top:2104px;left:0;width:1200px;height:455px;background:var(--grey)}
.card{position:absolute;top:200px;width:320px;height:172px;border:2px solid var(--blue);background:var(--white);padding:46px 22px 0;font-size:13px;line-height:23px;color:#444}
.card.active{background:var(--blue);color:var(--white)}
.card .q{position:absolute;left:141px;top:-19px;width:36px;height:36px;border-radius:50%;background:var(--green)}
.card .name{position:absolute;left:28px;top:190px;font-size:17px;font-weight:600;color:var(--green)}

/* trusted */
.trusted-photo{top:2563px;left:88px;width:464px;height:354px;background:linear-gradient(160deg,#f3efe9,#d9c2ac 60%,#b99a80)}
.trusted h2{position:absolute;left:601px;top:2608px;font-size:30px;color:var(--blue);font-weight:600}
.trusted h4{position:absolute;left:601px;top:2655px;width:470px;font-size:14px;line-height:26px;color:#222;font-weight:700}
.trusted p{position:absolute;left:601px;top:2715px;width:470px;font-size:13.5px;line-height:23px;color:#444}
.trusted .btn{position:absolute;left:601px;top:2835px}

/* footer */
.footer{top:2917px;left:0;width:1200px;height:336px;background:linear-gradient(135deg,#f7f7f7,#eef0f2);border-top:4px solid var(--blue)}
.partner{position:absolute;left:98px;top:148px;display:flex;align-items:center;gap:10px}
.partner i{width:36px;height:36px;border-radius:50%;background:var(--blue);display:block}
.partner span{font-size:34px;color:var(--blue);font-family:"Raleway",sans-serif;font-weight:500}
.fcol{position:absolute;top:50px}
.fcol h4{font-size:15px;color:var(--blue);font-weight:700;margin-bottom:22px}
.fcol li{list-style:none;font-size:14px;line-height:31px;color:#333}
.contact-row{display:flex;gap:16px;margin-bottom:18px;font-size:13px;line-height:19px;color:#333}
.contact-row i{width:36px;height:36px;border-radius:50%;border:2px solid var(--blue);flex:none;display:flex;align-items:center;justify-content:center}
.contact-row b{font-weight:700}
.field{border:1px solid #bbb;background:var(--white);font-size:12px;color:#555;padding:8px 10px;height:36px}
.send{background:var(--blue);color:var(--white);font-size:12px;font-weight:700;padding:11px 14px;display:inline-block}
.bottom{top:3253px;left:0;width:1200px;height:62px;background:#e6e6e6;font-size:13px;color:#333}
.bottom .copy{position:absolute;left:98px;top:22px}
.bottom .soc{position:absolute;left:873px;top:13px;display:flex;gap:12px}
.bottom .soc i{width:36px;height:36px;border-radius:50%;border:2px solid #333;display:block}
</style>
</head>
<body>

<header class="abs topbar">
  <div class="abs brand"><span class="brand-dot"></span><span class="brand-name">Bright Harbor</span></div>
  <div class="abs info" style="left:400px">
    <svg viewBox="0 0 34 34"><circle cx="17" cy="17" r="14" fill="none" stroke="#1d5fa8" stroke-width="3"/><path d="M17 9v9l6 4" stroke="#1d5fa8" stroke-width="3" fill="none"/></svg>
    <div><b>Monday - Friday 08:00 - 20:00</b><span>Saturday and Sunday - CLOSED</span></div>
  </div>
  <div class="abs info" style="left:686px">
    <svg viewBox="0 0 34 34"><rect x="8" y="3" width="18" height="28" rx="3" fill="none" stroke="#1d5fa8" stroke-width="3"/><circle cx="17" cy="26" r="2" fill="#1d5fa8"/></svg>
    <div><b>603-418-2290</b><span>info@brightharbormed.com</span></div>
  </div>
  <div class="abs info" style="left:912px">
    <svg viewBox="0 0 34 34"><path d="M4 20h10l-4-8 16 2c4 1 4 6 0 6h-4 4c3 0 3 5 0 5h-4c2 0 2 4 0 4H12c-5 0-8-3-8-9z" fill="none" stroke="#1d5fa8" stroke-width="2.5"/></svg>
    <div><b>Follow US</b><div class="socials"><i></i><i></i><i></i><i></i><i></i></div></div>
  </div>
</header>

<nav class="abs nav">
  <ul><li>HOME</li><li>PAGES</li><li>PORTFOLIO</li><li>BLOG</li><li>ELEMENTS</li><li>SHOP</li></ul>
  <div class="abs search"><svg width="18" height="18" viewBox="0 0 18 18"><circle cx="7.5" cy="7.5" r="5.5" fill="none" stroke="#333" stroke-width="2"/><path d="M11.5 11.5l5 5" stroke="#333" stroke-width="2"/></svg></div>
  <div class="abs book">BOOK APPOINTMENT</div>
</nav>

<section class="abs hero" role="img" aria-label="Photo of a smiling older couple with their granddaughter on a sunny beach">
  <h1>ADVANCED CARE PLANNING<br>SPECIALISTS</h1>
  <p>The focus of the company is Advanced Care Planning, ie planning for your future medical needs.</p>
  <span class="btn">Read More</span>
  <div class="arrows"><i></i><i></i></div>
</section>
<svg class="abs hero-curve" width="1200" height="130" viewBox="0 0 1200 130">
  <path d="M0 30 Q600 170 1200 30 L1200 130 L0 130Z" fill="#fff"/>
  <path d="M0 30 Q600 170 1200 30 L1200 46 Q600 150 0 46Z" fill="#3aa335"/>
</svg>

<div class="abs badge"></div>
<h2 class="abs section-title" style="top:775px">Welcome To Bright Harbor Medical Services</h2>
<p class="abs section-sub" style="top:830px">Nemo enim ipsam voluptatem quia voluptas sit aspernatur aut odit aut fugit, sed quia consequuntur magni dolores eos qui ratione voluptatem sequi nesciunt.</p>

<div class="abs features">
  <div class="feature">
    <svg viewBox="0 0 100 100"><path d="M50 48 C30 30 34 12 50 24 C66 12 70 30 50 48Z" fill="#1d5fa8"/><path d="M10 72h20l18 6h22l18-12c4-2 7 3 3 6L70 90H10z" fill="#3aa335"/><path d="M30 10l4 6M50 4v8M70 10l-4 6" stroke="#1d5fa8" stroke-width="3"/></svg>
    Individualized physician-guided health care planning.
  </div>
  <div class="feature">
    <svg viewBox="0 0 100 100"><rect x="34" y="8" width="36" height="36" rx="6" fill="#1d5fa8"/><path d="M52 16v20M42 26h20" stroke="#fff" stroke-width="6"/><path d="M10 72h20l18 6h22l18-12c4-2 7 3 3 6L70 90H10z" fill="#3aa335"/></svg>
    Helping navigate complex medical situations.
  </div>
  <div class="feature">
    <svg viewBox="0 0 100 100"><rect x="38" y="4" width="24" height="14" rx="3" fill="#1d5fa8"/><circle cx="50" cy="30" r="13" fill="#3aa335"/><path d="M22 96V66c0-12 12-20 28-20s28 8 28 20v30z" fill="#3aa335"/><path d="M40 50v22a8 8 0 0 0 16 0" stroke="#fff" stroke-width="4" fill="none"/></svg>
    Sharing your decisions with your loved ones and your doctor.
  </div>
</div>
<svg class="abs side-arrow" style="left:30px" width="30" height="54" viewBox="0 0 30 54"><path d="M26 2L4 27l22 25" stroke="#1d5fa8" stroke-width="3" fill="none"/></svg>
<svg class="abs side-arrow" style="left:1132px" width="30" height="54" viewBox="0 0 30 54"><path d="M4 2l22 25L4 52" stroke="#1d5fa8" stroke-width="3" fill="none"/></svg>

<section class="abs choose">
  <h2>CHOOSE CONFIDENTLY</h2>
  <h4>NEMO ENIM IPSAM VOLUPTATEM QUIA VOLUPTAS SIT AS PERNA TUR AUT ODIT AUT FUGIT</h4>
  <p>Lorem ipsum dolor sit amet, consectetuer. Proin gravida nibh vel velit auctor aliquet. Aenean sollicitudin, lorem quis bibendum auctor, nisi elit consequat ipsum, nec sagittis sem nibh id elit. Duis sed odio sit amet nibh vulputate cursus a sit amet mauris.</p>
  <span class="outline-btn">Read More</span>
  <div class="video" role="img" aria-label="Video still of a smiling family of four outdoors"><span class="play"></span></div>
</section>

<h2 class="abs section-title" style="top:1593px">Where People Come First</h2>
<p class="abs section-sub" style="top:1645px">Nemo enim ipsam voluptatem quia voluptas sit aspernatur aut odit aut fugit, sed quia consequuntur magni dolores eos qui ratione voluptatem sequi nesciunt.</p>

<svg class="abs" style="top:1780px;left:0" width="1200" height="110" viewBox="0 0 1200 110">
  <path d="M0 96 C120 80 160 40 230 45 S400 60 470 40 S620 20 730 48 S900 60 1000 40 S1140 70 1200 96" stroke="#1d5fa8" stroke-width="1.5" fill="none" stroke-dasharray="3 3"/>
</svg>
<div class="abs circles">
  <div class="circle-item" style="left:72px"><div class="ring"><div role="img" aria-label="Photo of a happy family" style="background:linear-gradient(135deg,#c9a98c,#8a5e43)"></div></div><h3>COMFORTABLE CARE</h3><p>Lorem ipsum dolor sit amet, con sectetuer elit.</p></div>
  <div class="circle-item" style="left:336px"><div class="ring"><div role="img" aria-label="Photo of a doctor with a young patient" style="background:linear-gradient(135deg,#d8c6c0,#9a6f63)"></div></div><h3>TRUSTED DOCTORS</h3><p>Lorem ipsum dolor sit amet, con sectetuer elit.</p></div>
  <div class="circle-item" style="left:601px"><div class="ring"><div role="img" aria-label="Photo of a smiling child" style="background:linear-gradient(135deg,#d89a7a,#7c4c36)"></div></div><h3>HIGHEST QUALITY</h3><p>Lorem ipsum dolor sit amet, con sectetuer elit.</p></div>
  <div class="circle-item" style="left:865px"><div class="ring"><div role="img" aria-label="Photo of a doctor taking notes" style="background:linear-gradient(135deg,#e9e6e3,#b8a89a)"></div></div><h3>GOOD HEALTH CARE</h3><p>Lorem ipsum dolor sit amet, con sectetuer elit.</p></div>
</div>

<section class="abs reviews">
  <h2 class="abs section-title" style="top:38px">What People Are Saying</h2>
  <p class="abs section-sub" style="top:90px">Nemo enim ipsam voluptatem quia voluptas sit aspernatur aut odit aut fugit, sed quia consequuntur magni dolores eos qui ratione voluptatem sequi nesciunt.</p>
  <div class="card" style="left:100px"><span class="q"></span>Lorem ipsum dolor sit amet, consectetur adipi scing elit, sed do eiusmod tempor incididunt ut labore et dolore magna aliqua. Ut enim ad minim veniam, quis nostrud exercitation.<span class="name">Glen R.</span></div>
  <div class="card active" style="left:440px"><span class="q"></span>Lorem ipsum dolor sit amet, consectetur adipi scing elit, sed do eiusmod tempor incididunt ut labore et dolore magna aliqua. Ut enim ad minim veniam, quis nostrud exercitation.<span class="name">Walter P.</span></div>
  <div class="card" style="left:780px"><span class="q"></span>Lorem ipsum dolor sit amet, consectetur adipi scing elit, sed do eiusmod tempor incididunt ut labore et dolore magna aliqua. Ut enim ad minim veniam, quis nostrud exercitation.<span class="name">Marion T.</span></div>
</section>

<div class="abs trusted-photo" role="img" aria-label="Photo of a smiling older couple embracing"></div>
<section class="trusted">
  <h2>TRUSTED DOCTORS</h2>
  <h4>NEMO ENIM IPSAM VOLUPTATEM QUIA VOLUPTAS SIT AS PERNA TUR AUT ODIT AUT FUGIT</h4>
  <p>Lorem ipsum dolor sit amet, consectetuer. Proin gravida nibh vel velit auctor aliquet. Aenean sollicitudin, lorem quis bibendum auctor, nisi elit consequat ipsum, nec sagittis sem nibh id elit. Duis sed odio sit amet nibh vulputate cursus a sit amet mauris.</p>
  <span class="btn">Read More</span>
</section>

<footer class="abs footer">
  <div class="partner"><i></i><span>lumenfold</span></div>
  <div class="fcol" style="left:375px"><h4>QUICK LINKS</h4><ul><li>› Home</li><li>› Pages</li><li>› Portfolio</li><li>› Blog</li><li>› Elements</li><li>› Contact Us</li></ul></div>
  <div class="fcol" style="left:560px"><h4>CONTACT US</h4>
    <div class="contact-row"><i><svg width="14" height="18" viewBox="0 0 14 18"><path d="M7 17s6-6 6-10A6 6 0 0 0 1 7c0 4 6 10 6 10z" fill="none" stroke="#1d5fa8" stroke-width="2"/><circle cx="7" cy="7" r="2" fill="#1d5fa8"/></svg></i><div><b>BRIGHT HARBOR,</b><br>48 Harbor Lane, Suite 2<br>Concord, NH 03301</div></div>
    <div class="contact-row"><i><svg width="12" height="18" viewBox="0 0 12 18"><rect x="1" y="1" width="10" height="16" rx="2" fill="none" stroke="#1d5fa8" stroke-width="2"/></svg></i><div><b>PHONE:</b><br>603-418-2290</div></div>
    <div class="contact-row"><i><svg width="18" height="14" viewBox="0 0 18 14"><rect x="1" y="1" width="16" height="12" fill="none" stroke="#1d5fa8" stroke-width="2"/><path d="M1 1l8 6 8-6" fill="none" stroke="#1d5fa8" stroke-width="2"/></svg></i><div><b>Mail:</b><br>info@brightharbormed.com</div></div>
  </div>
  <div class="fcol" style="left:813px;width:287px"><h4>CONTACT FORM</h4>
    <div style="display:flex;gap:10px;margin-bottom:10px"><div class="field" style="width:138px">Name</div><div class="field" style="width:139px">Phone</div></div>
    <div class="field" style="height:66px;margin-bottom:14px">Message</div>
    <span class="send">SEND MESSAGE</span>
  </div>
</footer>

<div class="abs bottom">
  <span class="copy">Copyright © 2016 Bright Harbor Medical Services. All Rights Reserved</span>
  <div class="soc"><i></i><i></i><i></i><i></i><i></i></div>
</div>

</body>
</html>
```